To promote our Catering Equipment services to our Laundry customers

Our company specialises in the supply, installation & maintenance of commercial laundry equipment, and we want a flyer that can be handed out to our laundry equipment customers to promote the fact that we also supply, rent, repair & service catering equipment as well (Catering equipment such as Cookers, Ovens etc)

Target Market(s)

The target market will be our existing customers. They trust us to repair their laundry equipment... why not trust us to do their catering equipment as well? Our customers are all business customers such as Care Homes for the elderly, Hotels etc.

Industry/Entity Type

Catering

Requirements
Must have
• Flyer will be approx. 216 x 139mm (To be confirmed) once we have a printer.
• It must include the www.brantleyservices-example.co.uk website address & our contact telephone number 0116 583 2901.
Nice to have
• Ideally it would pitch us a ' a one-stop shop' for all of their catering & laundry equipment needs.
• It might be better to be styled along a similar colour scheme as our website at www.brantleyservices-example.co.uk.

```html
<!DOCTYPE html>
<html lang="en">
<head>
<meta charset="utf-8">
<title>Brantley Services – Commercial Laundry &amp; Dishwasher Specialists</title>
<link href="https://fonts.googleapis.com/css2?family=Open+Sans:ital,wght@0,400;0,700;1,400;1,600;1,800&family=Carlito&display=swap" rel="stylesheet">
<style>
  :root {
    --backdrop: #e9e4dc;
    --paper: #ffffff;
    --brand-red: #e3161f;
    --ink: #1a1a1a;
    --gold: #f2b712;
    --link-blue: #1e5aa6;
    --white: #ffffff;
    --steel-light: rgba(236,239,243,.95);
    --steel-mid: rgba(170,178,188,.85);
  }
  * { box-sizing: border-box; margin: 0; padding: 0; }
  html, body { width: 902px; height: 1200px; overflow: hidden; }
  body { background: var(--backdrop); position: relative; font-family: "Open Sans", Arial, sans-serif; }

  .flyer { position: absolute; left: 53px; top: 38px; width: 797px; height: 1124px; background: var(--paper); box-shadow: 0 2px 10px rgba(0,0,0,.25); }

  .headline { position: absolute; left: 36px; top: 14px; font-style: italic; font-weight: 600; font-size: 55px; line-height: 76px; color: var(--brand-red); letter-spacing: .3px; }
  .headline .dark { color: var(--ink); }

  .side-band { position: absolute; left: 678px; top: 0; width: 119px; height: 1124px; background: var(--brand-red); }
  .side-band .slogan { position: absolute; left: 0; top: 320px; width: 119px; height: 784px; writing-mode: vertical-rl; transform: rotate(180deg); color: var(--white); font-style: italic; font-size: 28px; line-height: 39px; padding-right: 21px; white-space: nowrap; }

  .anniversary-badge { position: absolute; left: 602px; top: 152px; width: 136px; height: 136px; border-radius: 50%; background: var(--white); border: 6px solid var(--brand-red); box-shadow: 0 2px 5px rgba(0,0,0,.3); }
  .anniversary-badge::after { content: ""; position: absolute; inset: 14px; border-radius: 50%; background: radial-gradient(circle at 45% 40%, #3f7fc0, #123f7a); }

  .product-grid { position: absolute; left: 34px; top: 252px; width: 610px; height: 532px; display: grid; grid-template-columns: 305px 305px; grid-template-rows: 266px 266px; gap: 1px; background: var(--white); }
  .tile { position: relative; overflow: hidden; color: var(--white); }
  .tile--washers { background: linear-gradient(180deg, #d11820 0%, #a80f16 100%); }
  .tile--dryers { background: linear-gradient(180deg, #36c3e6 0%, #149fc6 100%); }
  .tile--ironers { background: linear-gradient(180deg, #7446a4 0%, #5a2e88 100%); }
  .tile--dishwashers { background: linear-gradient(180deg, #47ab45 0%, #2d8a31 100%); }
  .tile-floor { position: absolute; left: 0; right: 0; bottom: 0; height: 34px; background: linear-gradient(180deg, rgba(0,0,0,.55), rgba(0,0,0,.25)); }
  .tile-title { position: absolute; left: 14px; top: 14px; font-weight: 800; font-style: italic; font-size: 37px; line-height: 36px; letter-spacing: -1.8px; text-shadow: 0 0 2px rgba(0,0,0,.7), 2px 2px 3px rgba(0,0,0,.45); }
  .tile-claim { position: absolute; left: 12px; font-weight: 800; font-style: italic; font-size: 21px; line-height: 25px; letter-spacing: -1px; text-shadow: 0 0 2px rgba(0,0,0,.7), 1px 1px 2px rgba(0,0,0,.4); }
  .tile-button { position: absolute; left: 9px; top: 188px; width: 133px; height: 36px; border-radius: 7px; font-style: italic; font-size: 16px; line-height: 36px; padding-left: 12px; letter-spacing: -.6px; border: 1px solid rgba(255,255,255,.5); box-shadow: 0 2px 3px rgba(0,0,0,.3); z-index: 2; }
  .tile--washers .tile-button { background: linear-gradient(#e8575c, #c42a30); }
  .tile--dryers .tile-button { background: linear-gradient(#7fd6ea, #3ab2d2); }
  .tile--ironers .tile-button { background: linear-gradient(#a68ac6, #7a58a6); }
  .tile--dishwashers .tile-button { background: linear-gradient(#86c884, #4ea54e); }

  .product-photo { position: absolute; border-radius: 6px; box-shadow: 3px 4px 8px rgba(0,0,0,.35); }
  .tile--washers .product-photo { left: 158px; top: 96px; width: 128px; height: 148px; background: linear-gradient(100deg, var(--steel-mid), var(--steel-light) 35%, #c4cad2 70%, #4f6f9c 92%); }
  .tile--dryers .product-photo { left: 158px; top: 96px; width: 128px; height: 148px; background: linear-gradient(100deg, var(--steel-mid), var(--steel-light) 35%, #c4cad2 70%, #4f6f9c 92%); }
  .tile--ironers .product-photo { left: 146px; top: 180px; width: 150px; height: 86px; border-radius: 4px 4px 0 0; background: linear-gradient(180deg, #8d9bb8 0%, #3f4f72 45%, #2a3550 100%); }
  .tile--dishwashers .product-photo { left: 152px; top: 94px; width: 142px; height: 158px; background: linear-gradient(180deg, #4c6690 0%, #6d84a8 22%, var(--steel-light) 50%, #b9c1ca 100%); }

  .call-ribbon { position: absolute; left: 8px; top: 742px; width: 540px; height: 180px; }
  .call-ribbon svg { position: absolute; inset: 0; }
  .call-label { position: absolute; left: 52px; top: 48px; color: var(--white); font-size: 34px; font-weight: 400; }
  .call-number { position: absolute; left: 50px; top: 90px; color: var(--white); font-size: 58px; font-weight: 700; letter-spacing: .5px; }

  .company-name { position: absolute; left: 34px; top: 950px; width: 150px; height: 70px; display: flex; align-items: center; gap: 7px; font-family: "Carlito", Calibri, sans-serif; font-size: 25px; line-height: 26px; color: var(--brand-red); }
  .company-name .mark { width: 14px; height: 14px; background: var(--brand-red); flex: none; }
  .offer { position: absolute; left: 193px; top: 948px; width: 448px; font-family: "Carlito", Calibri, sans-serif; font-size: 16.6px; line-height: 26px; color: var(--ink); }
  .web-address { position: absolute; left: 36px; top: 1052px; font-size: 21px; letter-spacing: 1.6px; color: var(--link-blue); }
  .partner-name { position: absolute; left: 503px; top: 1035px; width: 141px; height: 67px; border: 2px solid var(--link-blue); display: flex; align-items: center; justify-content: center; text-align: center; font-family: "Carlito", Calibri, sans-serif; font-size: 17px; line-height: 19px; color: var(--link-blue); }
</style>
</head>
<body>
  <main class="flyer">
    <h1 class="headline">Commercial Laundry <span class="dark">&amp;</span><br>Dishwasher Specialists<br><span class="dark">in Your Area</span></h1>

    <aside class="side-band">
      <p class="slogan">They trust us to repair their laundry equipment…<br>why not trust us to do their catering equipment as well?</p>
    </aside>
    <div class="anniversary-badge" aria-hidden="true"></div>

    <section class="product-grid">
      <article class="tile tile--washers">
        <div class="tile-floor"></div>
        <div class="product-photo" role="img" aria-label="Commercial washing machine"></div>
        <h2 class="tile-title">Washing<br>Machines</h2>
        <p class="tile-claim" style="top:106px">Quality &amp;<br>Reliablity</p>
        <span class="tile-button">WASHERS</span>
      </article>
      <article class="tile tile--dryers">
        <div class="tile-floor"></div>
        <div class="product-photo" role="img" aria-label="Commercial tumble dryer"></div>
        <h2 class="tile-title">Tumble<br>Dryers</h2>
        <p class="tile-claim" style="top:106px">Highly<br>Efficient</p>
        <span class="tile-button">DRYERS</span>
      </article>
      <article class="tile tile--ironers">
        <div class="product-photo" role="img" aria-label="Rotary ironer machine"></div>
        <h2 class="tile-title">Rotary<br>Ironers</h2>
        <p class="tile-claim" style="top:104px">Robust<br>Build</p>
        <span class="tile-button">IRONERS</span>
      </article>
      <article class="tile tile--dishwashers">
        <div class="product-photo" role="img" aria-label="Commercial dishwasher with open rack of plates"></div>
        <h2 class="tile-title">Dishwashers</h2>
        <p class="tile-claim" style="top:76px">High<br>Cleaning<br>Standards</p>
        <span class="tile-button">DISHWASHERS</span>
      </article>
    </section>

    <div class="call-ribbon">
      <svg width="540" height="180" viewBox="0 0 540 180" aria-hidden="true">
        <defs>
          <linearGradient id="ribbonGold" x1="0" y1="0" x2="0" y2="1">
            <stop offset="0" stop-color="#f7c935"/>
            <stop offset="1" stop-color="#e9a70b"/>
          </linearGradient>
        </defs>
        <path d="M2 30 C2 10 20 4 42 4 L42 150 C22 150 8 158 6 170 Z" fill="#c98b06"/>
        <path d="M30 4 L470 4 L534 92 L470 170 L30 170 Z" fill="url(#ribbonGold)"/>
        <path d="M30 170 L470 170 L460 176 L34 176 Z" fill="#9a9a9a" opacity=".45"/>
      </svg>
      <p class="call-label">Call us on:</p>
      <p class="call-number">0116 583 2901</p>
    </div>

    <div class="company-name"><span class="mark"></span><span>Brantley Services</span></div>
    <p class="offer">We offer a wide range of new machines to rent or to buy – We can also repair all makes of existing equipment! Call us now to speak to one of our helpful staff.</p>
    <p class="web-address">www.brantleyservices-example.co.uk</p>
    <div class="partner-name">Ashby Catering Equipment</div>
  </main>
</body>
</html>
```